Colin Vardek Business card

Hey there, I’m hoping to have a business card designed. I’m in Real estate and just switched to a new Brokerage called: The Harbourline Property Group

The back could just be the company name maybe or whatever looks good!

I’ve attached some logos of our company and some cards my buddy had done up.

On the card:
Colin Vardek
colinvardek@mailora.com
587-412-9065
colinvardek.ca

Target Market(s)

Home buyers and sellers

Industry/Entity Type

Real Estate

Contact Information for Business Card

just looking for a cool and modern design with my picture on it. I like the idea of Black and red being used.

Requirements
Must have
• all the details provided. I'm open to anything. Just want a professional looking card.

```html
<!DOCTYPE html>
<html lang="en">
<head>
<meta charset="utf-8">
<title>Colin Vardek – Business Card</title>
<link href="https://fonts.googleapis.com/css2?family=Montserrat:wght@500;600;800&family=Roboto:wght@400;500&display=swap" rel="stylesheet">
<style>
  :root {
    --stage: #2b2b2d;
    --card: #222127;
    --card-deep: #1b1a1f;
    --red: #d01f3c;
    --white: #ffffff;
    --photo-a: #3a3336;
    --photo-b: #17161a;
  }
  * { box-sizing: border-box; margin: 0; padding: 0; }
  html, body { width: 1200px; height: 852px; overflow: hidden; }
  body {
    background: var(--stage);
    display: flex;
    flex-direction: column;
    align-items: center;
    justify-content: center;
    gap: 44px;
    font-family: "Roboto", sans-serif;
  }
  .card {
    position: relative;
    width: 620px;
    height: 354px;
    background: var(--card);
    border-radius: 22px;
    border: 3px solid var(--red);
    overflow: hidden;
    box-shadow: 0 18px 36px rgba(0,0,0,.45);
  }
  .card--back { margin-right: 200px; }
  .card--front { margin-left: 200px; }

  .brand {
    position: absolute;
    display: flex;
    align-items: center;
    gap: 14px;
    color: var(--white);
    font-family: "Montserrat", sans-serif;
    font-weight: 800;
    text-transform: uppercase;
    line-height: 1.05;
  }
  .brand__mark { width: 18px; height: 18px; background: var(--red); flex: none; }
  .card--back .brand { left: 70px; top: 132px; font-size: 34px; letter-spacing: .5px; }
  .card--back .brand__mark { width: 22px; height: 22px; }
  .card--back .shade {
    position: absolute; right: 0; top: 0; width: 260px; height: 100%;
    background: linear-gradient(120deg, var(--card) 0%, var(--card-deep) 100%);
  }

  .card--front .brand { left: 46px; top: 104px; font-size: 27px; }

  .portrait {
    position: absolute;
    right: 48px; top: 28px;
    width: 190px; height: 200px;
    background: radial-gradient(circle at 50% 35%, var(--photo-a) 0%, var(--photo-b) 80%);
  }
  .band {
    position: absolute;
    left: 170px; right: 0; top: 226px; height: 92px;
    background: var(--red);
    clip-path: polygon(5% 0, 100% 0, 100% 100%, 0 100%);
  }
  .name {
    position: absolute;
    right: 44px; top: 236px;
    color: var(--white);
    font-family: "Roboto", sans-serif;
    font-weight: 500;
    font-size: 22px;
  }
  .contacts {
    position: absolute;
    left: 210px; top: 252px;
    list-style: none;
    color: var(--white);
    font-size: 16px;
    line-height: 21px;
  }
  .contacts li { display: flex; align-items: center; gap: 8px; }
  .contacts svg { width: 13px; height: 13px; fill: var(--white); flex: none; }
</style>
</head>
<body>

  <section class="card card--back" aria-label="Card back">
    <div class="shade"></div>
    <div class="brand"><span class="brand__mark"></span><span>The Harbourline<br>Property Group</span></div>
  </section>

  <section class="card card--front" aria-label="Card front">
    <div class="brand"><span class="brand__mark"></span><span>The Harbourline<br>Property Group</span></div>
    <div class="portrait" role="img" aria-label="Portrait photo of Colin Vardek in a dark blazer and white shirt"></div>
    <div class="band"></div>
    <p class="name">Colin Vardek</p>
    <ul class="contacts">
      <li>
        <svg viewBox="0 0 24 24"><path d="M6.6 10.8a15 15 0 0 0 6.6 6.6l2.2-2.2a1 1 0 0 1 1-.25 11.4 11.4 0 0 0 3.6.57 1 1 0 0 1 1 1V20a1 1 0 0 1-1 1A17 17 0 0 1 3 4a1 1 0 0 1 1-1h3.5a1 1 0 0 1 1 1c0 1.25.2 2.45.57 3.57a1 1 0 0 1-.25 1z"/></svg>
        587-412-9065
      </li>
      <li>
        <svg viewBox="0 0 24 24"><path d="M2 5h20v14H2zm2 2v.4l8 5 8-5V7zm0 2.8V17h16V9.8l-8 5z"/></svg>
        colinvardek@mailora.com
      </li>
      <li>
        <svg viewBox="0 0 24 24"><path d="M12 2a10 10 0 1 0 0 20 10 10 0 0 0 0-20zm6.9 6h-3a15 15 0 0 0-1.3-3.9A8 8 0 0 1 18.9 8zM12 4c.8 1.1 1.5 2.5 1.9 4h-3.8c.4-1.5 1.1-2.9 1.9-4zM4.3 14a8 8 0 0 1 0-4h3.4a16 16 0 0 0 0 4zm.8 2h3a15 15 0 0 0 1.3 3.9A8 8 0 0 1 5.1 16zm3-8h-3a8 8 0 0 1 4.3-3.9A15 15 0 0 0 8.1 8zM12 20c-.8-1.1-1.5-2.5-1.9-4h3.8c-.4 1.5-1.1 2.9-1.9 4zm2.3-6H9.7a14 14 0 0 1 0-4h4.6a14 14 0 0 1 0 4zm.3 5.9a15 15 0 0 0 1.3-3.9h3a8 8 0 0 1-4.3 3.9zm1.7-5.9a16 16 0 0 0 0-4h3.4a8 8 0 0 1 0 4z"/></svg>
        colinvardek.ca
      </li>
    </ul>
  </section>

</body>
</html>
```